Website Performance Testing eBook for the software testing industry

Overview:
I would like an ebook/whitepaper designed. This ebook will be digital published on my website as a lead generation piece. The purpose is to give high level tips on what to look for and things to think about when working on a website performance testing project.
The ebook also demonstrates our expertise and knowledge on the topic.
Topic:
This is an ebook on software testing. Specifically, website performance testing.
About Veltrana:
Veltrana Solutions is an outsourcing development and software testing firm, and we provide expert services for application development, testing and data analytics. We extend our clients’ software testing capabilities with on-demand technical expertise. Our quality assurance resources work as part of our clients’ teams to help test applications on time and within budget.
Our model is designed to allocate the right mix of local and offshore resources in order to optimize expertise, speed and cost. We provide the ability to quickly add specialty skills to our client’s development team without them incurring long-term costs. The result is far better management of resource capacities and outcomes.
Background on our branding and previous pieces:
I have included a few of our previous ebooks and whitepapers. I like the look and feel of these pieces, however we have made updates to our brand guidelines since them, so the new brand guidelines will need to be incorporated, and I'd like to refresh/update what we have done in the past.
Refer to our website for an idea of our look and feel. This page is one of our newer sections and would be a good reference:
http://www.veltranasol.example/data-analytics/
Tone and feel:
- The look and feel should be professional, clean and polished.
- I like good use of whitespace.
- I would prefer to keep stock photography of people to a minimum. Any images should add to the content and be relevant to the content.
(Also, I uploaded some InDesign files in case you wanted to refer to those assets, but I didn't include the Links folder because they were too big. If there's anything you more you need, let me know)
Target Market(s)
Audience:
The audience is senior Quality Assurance and Software Testing professionals.
- 30-45 years old
- Technical mindset
- Interested in learning
Titles include
- QA Lead
- QA Manager
- QA Director
- Director or VP of Development
- QA Automation Engineer
Our customers are medium to large sized companies. Many are software companies, but many are also enterprises in all almost all industries.

```html
<!DOCTYPE html>
<html lang="en">
<head>
<meta charset="utf-8">
<title>Website Performance Testing — eBook</title>
<link rel="stylesheet" href="https://fonts.googleapis.com/css2?family=Open+Sans:wght@300;400&display=swap">
<style>
  :root {
    --brand-red: #dc3a30;
    --hero-dark: #4f4a48;
    --hero-mid: #9a5a4a;
    --hero-red: #d8412f;
    --text-grey: #6f6f6f;
    --label-grey: #b4b4b4;
    --white: #ffffff;
  }
  * { margin: 0; padding: 0; box-sizing: border-box; }
  html, body {
    width: 927px;
    height: 1200px;
    overflow: hidden;
    background: var(--white);
  }
  .cover {
    position: relative;
    width: 927px;
    height: 1200px;
    font-family: "Open Sans", Arial, sans-serif;
    background: var(--white);
  }
  .hero {
    position: absolute;
    left: 0; top: 0;
    width: 927px;
    height: 708px;
    background:
      radial-gradient(ellipse 420px 300px at 220px 170px, rgba(176,110,90,0.55), transparent 70%),
      linear-gradient(100deg, var(--hero-dark) 0%, #6a524a 22%, var(--hero-mid) 45%, #c4503c 70%, var(--hero-red) 100%);
  }
  .hero-rule {
    position: absolute;
    left: 107px;
    top: 164px;
    width: 2px;
    height: 436px;
    background: var(--white);
  }
  .hero-title {
    position: absolute;
    left: 163px;
    top: 248px;
    color: var(--white);
    font-weight: 300;
    font-size: 77px;
    line-height: 88px;
    letter-spacing: 0.5px;
    text-transform: uppercase;
  }
  .intro {
    position: absolute;
    left: 108px;
    top: 812px;
    width: 700px;
    color: var(--text-grey);
    font-size: 14.6px;
    line-height: 21.5px;
    font-weight: 400;
  }
  .doc-type {
    position: absolute;
    left: 54px;
    top: 1120px;
    color: var(--label-grey);
    font-size: 23px;
    font-weight: 300;
  }
  .brand-name {
    position: absolute;
    right: 55px;
    top: 1030px;
    color: var(--brand-red);
    font-size: 56px;
    line-height: 54px;
    font-weight: 400;
    text-align: right;
    text-transform: lowercase;
  }
</style>
</head>
<body>
  <main class="cover">
    <div class="hero" role="img" aria-label="Red-tinted photo of a tablet displaying a website analytics dashboard beside a coffee cup"></div>
    <div class="hero-rule"></div>
    <h1 class="hero-title">Website<br>Performance<br>Testing</h1>

    <p class="intro">Like any software product, your website or web application requires thorough testing before it goes live to ensure a quality user experience. Web users are accustomed to a high level of functionality, responsiveness and usability. Increasingly, they lack patience for web sites that do not provide a fulfilling experience. Thus, testing the performance aspects of your website is critical.</p>

    <div class="doc-type">ebook</div>
    <div class="brand-name">Veltrana<br>Solutions</div>
  </main>
</body>
</html>
```